A new website is needed for a breakthrough creative thinking tool

My name is Rob Telford - i have a PhD in Organisational Creativity and have written a few books on creative & speed thinking. You can check me out by visiting www.drrobtelford.example

I have uncovered an amazing insight of what stops most people from being more creative.

Themselves.

They filter & judge their own rich, new ideas. I have found the best way to overcome this self-limiting behaviour is to encourage people to think of ideas really quickly so they have no time to judge - they just create.

I call this accelerated form of creativity - Speed Thinking and the tool i have developed is Notion Sprint. There are 5 steps - Start, enhance, connect, evaluate & action.

The most important step is the start where i ask each person to create 9 ideas in 2 minutes using a visual bubble format (see the uploaded file). For many people this magic formula (my wording) is the very essence of an Notion Sprint.

I have also developed a new mobile app (phone & tablet) which you can find here -

http://lnk.example/7QpR2mX

I wish to develop a new word press site which promotes Notion Sprint.

My vision is to have all the world Blitzing. In a time-poor world where students, managers, leaders & small business owners are being asked to be more creative, innovative and do more with less - we need better, faster tools.

Notion Sprint is an ideal tool for this new world.

I passionately believe in the power of Notion Sprint to unlock amazing creativity in the most logical of people.

I have tested this new tool with thousands of people across Australia, Asia and the US.

I would like to develop a web site which is as creative as the tool itself. My aim is top create a site that explains the concept of an Notion Sprint through the use of videos, blogs and refer visitors to the new mobile app.

I would like this site to be talked about and help to create a movement of Blitzers around the world.

Notion Sprint is the next great creative thinking tool after Brainstorming (developed 70 years ago) & Mindmapping (developed 30 years ago).

Notion Sprint can be used by an individual, partner or group.

The key benefits of using an Notion Sprint are:
- It is a simple, practical, effective way of unlocking the creativity of everyone.
- Notion Sprint is fast & time efficient.
- It helps people who procrastinate to get started (some 20-25% of the adult population are chronic procrastinators; 70% plus for students).
- It enables everyone in group work to contribute their ideas because each person has to create 9 ideas in 2 minutes
- People feel more confident and energised and
- It accelerates progress
Updates

this brief is for a design only

someone else will build the word press site
thanks rob

Reason: Some of the designs are close but require some more work as per my feedback. thanks rob

As part of my requirements i would also like to see 2-3 website pages other than the homepage.

thanks rob

Target Market(s)

This is a mass market product.

But it is a new concept.

Think how Cerebrant is trying to position and sell their brain training games.

Any student, manager, leader or small business owner can use this tool/app.

In large organisations it would engage and interest anyone involved in marketing, innovation, advertising, research, HR, new product development, customer service, training, sales etc.

The people who are most interested in my work have a particular mindset - they are open to new ideas, want to challenge the status quo, welcome change, like learning, sharing and collaborating.

The other segment are those people who are interested in helping others to reach their potential e.g. teachers, trainers, facilitators, coaches etc.

Industry/Entity Type

Small Business

Requirements
Must have
• The Notion Sprint web site design should be clean, simple and answer the following questions:

- What is an Notion Sprint? A breakthrough thinking tool and app that overcomes the biggest barrier that stops most people from being more creative ( or reaching their full creative potential) - i.e. their own internal judging, critical voice.

It's your mobile creative system.

- Who should Sprint? High School right through to university students, small business owners, managers & leaders.

When to Sprint: You can Sprint at any time - in a bus, train, subway, work in the class room. But here are some specific examples
- In a brainstorming, ideation, planning session
- In group work
- You can use as a weekly to do list
- When you need to solve a problem or generate an idea
- You have a flash of inspiration and want to capture an idea or make an existing idea 9 times better
- To do an initial structure an essay, project, assignment, presentation or speech.
- To summarise a topic etc etc etc
Nice to have
• I have an existing web site www.drrobtelford.example

It might be useful to have a potential visual link with this site but this is a nice to have.

The bubbles (see the uploaded file) are an important part of the Notion Sprint tool so this might be worth highlighting in some way (the bubbles help users to make connections and escape thinking in a logical, structured, list type way).

```html
<!DOCTYPE html>
<html lang="en">
<head>
<meta charset="utf-8">
<title>Dr Rob Telford – Notion Sprint</title>
<link rel="stylesheet" href="https://fonts.googleapis.com/css2?family=Signika:wght@400;600&family=Raleway:wght@400;600&family=Montserrat:wght@600&display=swap">
<style>
:root{
  --dark:#2d2d2d;
  --green:#5f8f2e;
  --green-dark:#4a7222;
  --red:#c8202b;
  --orange:#e8892a;
  --orange-text:#e07a16;
  --blue:#1e96c8;
  --blue-dark:#1781b0;
  --text:#4a4a4a;
  --rule:#d8d8d8;
}
*{box-sizing:border-box;margin:0;padding:0}
html,body{width:776px;height:1200px;overflow:hidden;background:#fff}
body{font-family:"Raleway",sans-serif;color:var(--text);font-size:7.6px;line-height:1.5}
.page{position:relative;width:776px;height:1200px;overflow:hidden}
.abs{position:absolute}

/* header */
.site-header{left:0;top:0;width:776px;height:70px;background:linear-gradient(#3a3a3a,#262626)}
.brand{left:150px;top:16px;display:flex;align-items:center;gap:10px}
.brand-dot{width:22px;height:22px;border-radius:50%;background:var(--orange)}
.brand-name{font-family:"Montserrat",sans-serif;font-weight:600;color:#fff;font-size:15px;letter-spacing:3px;line-height:1}
.brand-tag{font-family:"Montserrat",sans-serif;font-weight:600;color:#fff;font-size:9px;margin-top:6px;opacity:.85}
.search{left:535px;top:26px;width:95px;height:18px;background:#555;border:1px solid #666;border-radius:2px;color:#ccc;font-size:7px;padding:3px 4px}
.search svg{position:absolute;right:4px;top:4px}

.main-nav{left:0;top:70px;width:776px;height:26px;background:linear-gradient(#72a53a,var(--green))}
.main-nav ul{list-style:none;display:flex;position:absolute;left:145px;top:0;height:26px}
.main-nav li{width:48.5px;text-align:center;color:#fff;font-size:7px;line-height:26px;border-left:1px solid #4a7222}
.main-nav li:last-child{border-right:1px solid #4a7222}

/* hero */
.hero{left:0;top:96px;width:776px;height:242px;background:radial-gradient(ellipse at 50% 45%,#1e6478 0%,#0e3a48 40%,#061b22 100%)}
.hero-art{left:170px;top:118px;width:436px;height:110px;background:radial-gradient(ellipse at 50% 50%,rgba(70,170,215,.35) 0%,rgba(40,130,175,.18) 55%,rgba(0,0,0,0) 75%)}
.hero-title{left:0;width:776px;text-align:center;font-family:"Signika",sans-serif;font-weight:600;font-size:24px;line-height:1}
.hero-title.t1{top:259px;color:var(--orange)}
.hero-title.t2{top:285px;color:#7fa33a}
.hero-line{left:0;top:338px;width:776px;height:3px;background:var(--orange)}

/* intro */
.section-title{font-family:"Signika",sans-serif;font-weight:400;color:var(--red);font-size:12.5px}
.intro-title{left:155px;top:367px}
.intro-text{left:155px;top:390px;width:320px}
.intro-sub{left:155px;top:437px;width:320px}
.intro-sub b{color:var(--green);font-weight:600;display:block}

.video{left:155px;top:483px;width:315px;height:145px;background:linear-gradient(90deg,#1c2a2a 0%,#31413f 55%,#8b7c6c 80%,#3a4a48 100%)}
.video-title{left:188px;top:489px;color:#2ab6e6;font-family:"Signika",sans-serif;font-size:9px;background:rgba(0,0,0,.55);padding:0 3px}
.video-from{left:192px;top:502px;color:#fff;font-size:5.5px}
.video-from span{color:#2ab6e6}
.video-icon{left:160px;top:488px;width:24px;height:24px;border-radius:50%;background:#2a6ad8}
.video-caption{left:190px;top:536px;width:170px;text-align:center;font-family:"Signika",sans-serif}
.video-caption .a{color:#eee;font-size:10.5px}
.video-caption .b{color:#7ea33a;font-size:17px;font-weight:600;line-height:1.1}
.video-side{left:443px;top:483px;width:27px;height:120px;background:rgba(0,0,0,.7);color:#fff;font-size:4px;text-align:center;padding-top:6px}
.video-side div{margin-bottom:9px}
.video-bar{left:155px;top:605px;width:315px;height:23px;background:rgba(0,0,0,.75)}
.video-play{left:159px;top:607px;width:22px;height:18px;background:#222}
.video-time{left:190px;top:604px;font-size:5px;color:#fff;background:#333;padding:0 2px}
.video-track{left:200px;top:614px;width:176px;height:4px;background:#444}
.video-brand{left:430px;top:610px;color:#fff;font-weight:600;font-size:7px}

/* benefits */
.benefits{left:486px;top:365px;width:139px;height:263px;border:1px solid #e2e2e2;background:#fff}
.benefits-head{left:486px;top:365px;width:139px;height:36px;background:linear-gradient(#d7272f,#b01a22);color:#fff;font-family:"Signika",sans-serif;font-size:10px;text-align:center;line-height:1.15;padding-top:6px}
.benefits ul{position:absolute;left:6px;top:48px;width:124px;list-style:none}
.benefits li{font-size:6.3px;line-height:1.55;color:#333;padding-left:9px;position:relative;margin-bottom:8px}
.benefits li::before{content:"";position:absolute;left:0;top:2px;width:5px;height:5px;border-radius:50%;border:1.3px solid var(--orange)}

/* tiles */
.tile{top:645px;height:73px;color:#fff;padding:6px 6px}
.tile h3{font-family:"Signika",sans-serif;font-weight:400;font-size:9.5px;margin-bottom:7px}
.tile p{font-size:7px;line-height:1.6}
.tile.who{left:153px;width:150px;background:var(--orange)}
.tile.when{left:320px;width:150px;background:var(--green)}
.tile.app{left:486px;width:140px;background:linear-gradient(#2aa8e0,#0d7fbf);padding:0}
.app-square{left:10px;top:12px;width:48px;height:48px;background:#1478c8;border-radius:9px;border:2px solid #fff}
.app-text{left:66px;top:20px;font-family:"Signika",sans-serif;font-size:11px;line-height:1.1}
.app-text small{display:block;font-family:"Raleway",sans-serif;font-size:6.5px;margin-top:2px}

/* blog */
.blog-title{left:153px;top:734px;font-family:"Signika",sans-serif;font-weight:600;font-size:21px;color:var(--blue);letter-spacing:.3px}
.post-img{left:158px;width:124px;height:80px;border:3px solid #fff;box-shadow:0 1px 3px rgba(0,0,0,.35)}
.post-img.p1{top:778px;background:linear-gradient(#8a5a3a,#c89a6a 60%,#3a2418)}
.post-img.p2{top:930px;background:linear-gradient(#eef7fb,#d3ecf6)}
.post-body{left:291px;width:180px}
.post-body h4{font-family:"Signika",sans-serif;font-weight:400;color:var(--orange-text);font-size:13.2px;line-height:1.1}
.post-date{color:var(--green);font-size:6.5px;margin:4px 0 6px}
.post-date b{font-weight:600}
.post-body p{font-size:7.3px;line-height:1.6}
.more{display:inline-block;background:linear-gradient(#d82a30,#a81a20);color:#fff;font-weight:600;font-size:6.5px;padding:3px 10px;border-radius:2px;margin-top:6px}
.rule{left:155px;width:313px;height:1px;background:var(--rule)}

/* bio */
.bio{left:486px;top:736px;width:139px;height:306px;border:1px solid #e2e2e2;background:#fff}
.bio-photo{left:14px;top:6px;width:120px;height:92px;background:radial-gradient(ellipse at 55% 40%,#e4c3a8 0%,#9cb8d8 50%,#fff 72%)}
.bio-badge{left:10px;top:9px;width:40px;height:40px;border-radius:50%;background:var(--red);color:#fff;font-family:"Signika",sans-serif;font-size:9px;line-height:1;padding:10px 0 0 9px}
.bio-text{left:14px;top:106px;width:112px;text-align:center;font-size:6.3px;line-height:1.85}
.bio-btn{left:12px;top:278px;width:118px;height:17px;background:linear-gradient(#6aa03a,var(--green-dark));color:#fff;font-size:6.3px;font-weight:600;text-align:center;line-height:17px;border-radius:2px}

/* footer */
.site-footer{left:0;top:1065px;width:776px;height:135px;background:var(--blue);border-top:4px solid var(--blue-dark)}
.foot-col{top:1089px;color:#fff}
.foot-col h5{font-weight:600;font-size:8px;margin-bottom:9px}
.foot-col li{list-style:none;font-size:7.5px;line-height:1.95}
.foot-col p{font-size:7.3px;line-height:1.6;width:125px}
.foot-input{width:117px;height:17px;background:#fff;border:1px solid #ccc;margin-top:8px}
.foot-btn{width:79px;height:16px;background:linear-gradient(#6aa03a,var(--green-dark));color:#fff;font-size:6.5px;font-weight:600;text-align:center;line-height:16px;margin-top:4px}
.social li{display:flex;align-items:center;gap:8px;line-height:1;margin-bottom:6px}
.social span{width:12px;height:12px;border-radius:50%;background:#fff;display:inline-block}
</style>
</head>
<body>
<div class="page">

  <header class="abs site-header"></header>
  <div class="abs brand">
    <div class="brand-dot"></div>
    <div>
      <div class="brand-name">DR ROB TELFORD</div>
      <div class="brand-tag">Unleash ideas, innovation &amp; growth – now!</div>
    </div>
  </div>
  <div class="abs search">Search
    <svg width="9" height="9" viewBox="0 0 10 10"><circle cx="4" cy="4" r="3" fill="none" stroke="#ddd" stroke-width="1.3"/><line x1="6.2" y1="6.2" x2="9" y2="9" stroke="#ddd" stroke-width="1.5"/></svg>
  </div>

  <nav class="abs main-nav">
    <ul><li>BLOG</li><li>ABOUT ROB</li><li>TOOLS</li><li>SPEAK</li><li>CONSULT</li><li>FACILITATE</li><li>TRAIN</li><li>NPD</li><li>BOOKS</li><li>CONTACT</li></ul>
  </nav>

  <section class="abs hero"></section>
  <div class="abs hero-art" role="img" aria-label="Illustration of nine numbered idea bubbles arranged in a ring on a dark teal glowing background"></div>
  <h1 class="abs hero-title t1">NOTION SPRINT - SPEED THINKING</h1>
  <h2 class="abs hero-title t2">9 IDEAS IN 2 MINUTES</h2>
  <div class="abs hero-line"></div>

  <h2 class="abs section-title intro-title">WHAT IS A NOTION SPRINT?</h2>
  <p class="abs intro-text">A breakthrough thinking tool and app that overcomes the biggest barrier that stops most people from being more creative ( or reaching their full creative potential) - i.e. their own internal judging, critical voice.</p>
  <p class="abs intro-sub"><b>How to run a Sprint</b>There are 5 steps to run a Sprint:<br>Start, Enhance, Connect, Evaluate &amp; Action.</p>

  <div class="abs video" role="img" aria-label="Video still of Dr Rob Telford speaking"></div>
  <div class="abs video-icon"></div>
  <div class="abs video-title">Dr Rob Telford discusses his creative insight</div>
  <div class="abs video-from">from <span>Pinch Studio</span></div>
  <div class="abs video-caption"><div class="a">Watch Dr Rob Discuss his</div><div class="b">CREATIVE INSIGHT</div></div>
  <div class="abs video-side"><div>♥<br>LIKE</div><div>◷<br>LATER</div><div>➚<br>SHARE</div></div>
  <div class="abs video-bar"></div>
  <div class="abs video-play"><svg width="22" height="18"><polygon points="8,5 8,13 15,9" fill="#fff"/></svg></div>
  <div class="abs video-time">02:07</div>
  <div class="abs video-track"></div>
  <div class="abs video-brand">reelhost</div>

  <aside class="abs benefits">
    <ul>
      <li>It is a simple, practical, effective way of unlocking the creativity of everyone.</li>
      <li>Notion Sprint is fast &amp; time efficient.</li>
      <li>It helps people who procrastinate to get started (some 20-25% of the adult population are chronic procrastinators; 70% plus for students).</li>
      <li>It enables everyone in group work to contribute their ideas because each person has to create 9 ideas in 2 minutes</li>
      <li>People feel more confident and energised and</li>
      <li>It accelerates progress</li>
    </ul>
  </aside>
  <div class="abs benefits-head">KEY BENEFITS OF<br>NOTION SPRINT</div>

  <div class="abs tile who"><h3>Who should Sprint?</h3><p>High School right through to university students, small business owners, managers &amp; leaders.</p></div>
  <div class="abs tile when"><h3>When to Sprint?</h3><p>You can Sprint at any time - in a bus, train, subway, work in the class room.</p></div>
  <div class="abs tile app">
    <div class="abs app-square"></div>
    <div class="abs app-text">DOWNLOAD<br>Mobile App<small>(phone &amp; tablet)</small></div>
  </div>

  <h2 class="abs blog-title">THE LATEST FROM DR ROB'S BLOG</h2>

  <div class="abs post-img p1" role="img" aria-label="Photo of a crowd raising their hands"></div>
  <article class="abs post-body" style="top:774px">
    <h4>TO BUILD AN INNOVATION CULTURE YOU NEED MORE CREATIVE CONVERSATIONS</h4>
    <div class="post-date">Posted on <b>11/15/ 2013</b></div>
    <p>It is not enough to generate big, new ideas if no-one is open to them. Innovative cultures are built on the back of creative conversations. Here's how to conduct one.</p>
    <span class="more">MORE</span>
  </article>
  <div class="abs rule" style="top:914px"></div>

  <div class="abs post-img p2" role="img" aria-label="Notion Sprint app splash screen, the world's fastest creativity and productivity tool"></div>
  <article class="abs post-body" style="top:928px">
    <h4>WHEN TO CALL A NOTION SPRINT?</h4>
    <div class="post-date">Posted on <b>11/14/ 2013</b></div>
    <p>Notion Sprint is a powerful creative thinking tool we have developed –here is when to use it from an experienced HR professional.</p>
    <span class="more">MORE</span>
  </article>
  <div class="abs rule" style="top:1042px"></div>

  <aside class="abs bio">
    <div class="abs bio-photo" role="img" aria-label="Portrait photo of Dr Rob Telford"></div>
    <div class="abs bio-badge">Dr.<br>Rob</div>
    <p class="abs bio-text">Dr. Rob Telford is one of the most creative thinkers, speakers &amp; consultants in Australia. He specialises in unlocking creativity and innovation in individuals, groups &amp; teams – quickly!<br><br>Dr. Telford has been interviewed by Enterprise Review Weekly, National Talk Radio, The Southern Financial Ledger, Chief Magazine and contributed articles for Brandcraft Magazine, People Monthly, Forward Company and Quick Minds.</p>
    <div class="abs bio-btn">MORE ABOUT DR. ROB TELFORD</div>
  </aside>

  <footer class="abs site-footer"></footer>
  <div class="abs foot-col" style="left:155px">
    <h5>HOW CAN ROB HELP YOU?</h5>
    <ul><li>Notion Sprint</li><li>Sprint Pro</li><li>Speed Thinking</li><li>Speaking</li><li>Books</li></ul>
  </div>
  <div class="abs foot-col" style="left:325px">
    <h5>JOIN THE COMMUNITY</h5>
    <p>Sign up for regular updates and get a free E Book on 36 Innovation tips</p>
    <div class="foot-input"></div>
    <div class="foot-btn">SIGNUP NOW</div>
  </div>
  <div class="abs foot-col social" style="left:486px">
    <h5>FOLLOW DR. ROB TELFORD</h5>
    <ul><li><span></span>Circlebook</li><li><span></span>Chirper</li><li><span></span>ProNet</li></ul>
  </div>

</div>
</body>
</html>
```